New Corporate Email Signature with Custom GIF KAV Electric LLC & KAV Fire & Security

Project Overview
KAV Electric LLC and KAV Fire & Security are seeking a professional, polished, and technically robust corporate email signature design. The project has two integrated deliverables:
A custom animated GIF representing both sides of our business
A complete corporate email signature layout designed for real-world compatibility (Gmail, Outlook, iOS, Android)
Our brand aesthetic is corporate, conservative, and clean. We value clarity, trust, professionalism, and subtle creativity β€” nothing overly flashy or cartoonish.
This design will be used across the entire company and must be visually aligned with our brand while remaining technically dependable.

PART 1 β€” Animated GIF Requirements
The GIF will be the core visual anchor of the new signature.
It must be clean, smooth, subtle, and optimized for email use.
βš™ Technical Requirements
Max file size: 150–200 KB (smaller is better)
Dimensions: approx 300px width (flexible, but must look good small)
Looping: continuous loop
Style: professional, minimalistic transitions

No rapid flashing or harsh animations
Must export cleanly into a format email clients accept

🎞 GIF Animation Sequence
Phase 1 β€” KAV Electric (KE)
Use the yellow β€œKE” avatar logo (provided).
Animation flow:
KE avatar appears
Full name β€œKAV Electric LLC” slides in, fades in, or otherwise appears smoothly
A scrolling or cycling list of service offerings displays:
EV Charging Stations
Generator & Transformers
Testing & Troubleshooting
LED Lighting Upgrades
After the list is shown, the entire KE segment fades out

Phase 2 β€” KAV Fire & Security (KF)
Use the red β€œKF” avatar logo (provided).
Animation flow mirrors Phase 1:
KF avatar appears
Full name β€œKAV Fire & Security” slides/fades in
Scrolling or cycling list of services displays:
Fire Alarm Upgrades
BQTL 48 Test & Inspect
Security Surveillance Systems
Access Control Systems
Data & Fiber Optic Cabling
Fade out β†’ loop back to KE
Creative Direction

Designers are encouraged to use:
Clean transitions
Soft fades
Professional typography
Modern minimalism
Consistent brand colors
High clarity at small sizes

Avoid:
Busy motion
Hard flashes
Excessive text overlays
Overly long transitions

The goal: a smooth, corporate-grade rotation that fits seamlessly into an email signature.

PART 2 β€” Corporate Email Signature Design

The signature must be visually appealing, brand-aligned, and structurally bulletproof across all major email systems.
πŸ“ Required Elements
πŸ‘€ Left Side Content
Circular headshot (we will supply final photos)
Social media icons with embedded URLs:
Facebook
LinkedIn
Google Business Profile
Instagram

Icons should be clean, modern, and in alignment with brand colors
πŸ“„ Right Side Content
Name
Title
KAV Electric LLC / KAV Fire & Security (depending on user)
Phone number
Email address
License# 52804
Physical office address: 384 Pembrook St, Westwood NJ 07912

Small CTA for newsletter signup (button or micro-banner)

🏒 Branding Assets Provided

You will receive:
KE avatar logo
KF avatar logo
Full-name KE logo
Full-name KF logo

These should be incorporated naturally and professionally.

Design Requirements

Conservative corporate styling

Clean typography

Balanced use of white space

Professional hierarchy

Light and dark mode compatibility preferred

Layout should not rely on one large image

All images should export cleanly for hosting on servers/CDN

Avoid overly tall signatures

The final signature must present as modern, trustworthy, and technically reliable across platforms.

πŸ§ͺ Compatibility Requirements

The signature must display correctly in:

Gmail (web and mobile)

Outlook (desktop & online)

Apple Mail

iPhone Mail

Android mail apps

Designers must avoid DIV-based layouts and instead propose a layout that can be implemented using table-based HTML, which is the industry standard for email compatibility.

You do not need to build the HTML β€” only supply the final layered design (PSD/AI/Figma) plus a clear structural layout that can be converted to HTML later.

πŸ“¦ Deliverables
1. Animated GIF

Final optimized GIF

Source file (After Effects, Photoshop, or equivalent)

Export guidelines so we can reproduce future versions

2. Email Signature Design

Full static design mockup

Modular layout for each employee

Icon set for social media

Newsletter CTA element

Clear spacing, alignment, and typography specifications

All source files (PSD, AI, Figma, etc.)

🧭 Creative Guidance Summary

We want:
βœ” Modern
βœ” Corporate
βœ” Minimalistic
βœ” Professional
βœ” Clean motion
βœ” Consistent branding
βœ” Email-safe elements

We do not want:
✘ Flashy marketing look
✘ Overly colorful or playful styles
✘ Hard-to-read fonts
✘ Heavy animation
✘ Oversized signatures

πŸ›  Tools & Format Flexibility

We allow full creative freedom regarding:

Animation style

Typography choices

Structuring of the two-column layout

How the service lists scroll or cycle

As long as the end result is clean, brand-aligned, professional, and email-compatible.

πŸ’¬ Final Note to Designers

We encourage creativity within the boundaries of corporate professionalism.
This signature will represent our company every time an email is sent β€” it must communicate trust, clarity, expertise, and brand strength.

```html
<!DOCTYPE html>
<html lang="en">
<head>
<meta charset="utf-8">
<title>KAV Fire &amp; Security – Email Signature</title>
<link href="https://fonts.googleapis.com/css2?family=Poppins:wght@400;500;600&display=swap" rel="stylesheet">
<style>
  :root {
    --page: #ffffff;
    --brand-red: #e0101a;
    --dark-bg-a: #5f5f5f;
    --dark-bg-b: #767676;
    --light-bg-a: #d9d9d9;
    --light-bg-b: #ececec;
    --bar-grey-dark: #8a8a8a;
    --bar-grey-light: #7d7d7d;
    --ink-light: #ffffff;
    --ink-dark: #111111;
    --photo-a: #f3c9a6;
    --photo-b: #2c3442;
  }
  * { margin: 0; padding: 0; box-sizing: border-box; }
  html, body { width: 1200px; height: 888px; overflow: hidden; background: var(--page); }
  body { position: relative; font-family: "Poppins", sans-serif; }

  .signature {
    position: absolute; left: 87px; width: 1026px; height: 342px; overflow: hidden;
  }
  .signature--dark { top: 76px; background: linear-gradient(120deg, var(--dark-bg-a), var(--dark-bg-b) 55%, var(--dark-bg-a)); color: var(--ink-light); }
  .signature--light { top: 466px; background: linear-gradient(120deg, var(--light-bg-a), var(--light-bg-b) 50%, var(--light-bg-a)); color: var(--ink-dark); }

  .pedestal { position: absolute; left: 0; top: 0; }

  .headshot {
    position: absolute; width: 168px; height: 168px; border-radius: 50%;
    border: 8px solid #fff;
    background: radial-gradient(circle at 50% 38%, var(--photo-a) 0 38%, var(--photo-b) 62%);
  }
  .signature--dark .headshot { left: 149px; top: 56px; }
  .signature--light .headshot { left: 131px; top: 36px; }

  .social { position: absolute; display: block; width: 40px; height: 40px; border-radius: 50%; background: var(--brand-red); }

  .details { position: absolute; left: 643px; top: 0; }
  .signature--light .details { left: 646px; }
  .detail {
    position: absolute; left: 0; display: flex; align-items: center; gap: 8px;
    font-size: 18px; font-weight: 400; white-space: nowrap; transform: translateY(-50%);
  }
  .detail svg { width: 16px; height: 16px; fill: currentColor; flex: none; }
  .company { font-size: 21px; font-weight: 600; letter-spacing: 3.5px; text-transform: uppercase; }

  .subscribe {
    position: absolute; top: 256px; width: 274px; height: 45px; border-radius: 23px;
    background: var(--brand-red); color: #fff; font-size: 20px; font-weight: 500;
    display: flex; align-items: center; justify-content: center; text-decoration: none;
  }
  .signature--dark .subscribe { left: 646px; }
  .signature--light .subscribe { left: 650px; }
</style>
</head>
<body>

<section class="signature signature--dark" aria-label="Email signature, dark version">
  <svg class="pedestal" width="1026" height="342" aria-hidden="true">
    <polygon points="80,188 389,188 397,210 72,210" fill="var(--brand-red)"/>
    <rect x="51" y="217" width="363" height="10" fill="var(--bar-grey-dark)"/>
  </svg>
  <div class="headshot" role="img" aria-label="Circular headshot of the employee"></div>

  <a class="social" href="#" aria-label="Social profile link 1" style="left:134px;top:248px"></a>
  <a class="social" href="#" aria-label="Social profile link 2" style="left:183px;top:248px"></a>
  <a class="social" href="#" aria-label="Social profile link 3" style="left:233px;top:248px"></a>
  <a class="social" href="#" aria-label="Social profile link 4" style="left:283px;top:248px"></a>

  <div class="details">
    <p class="detail" style="top:39px"><svg viewBox="0 0 16 16"><circle cx="8" cy="4.5" r="3.5"/><path d="M1 16c0-4 3-6.5 7-6.5s7 2.5 7 6.5z"/></svg>Alan Mercer</p>
    <p class="detail company" style="top:75px">KAV Fire &amp; Security</p>
    <p class="detail" style="top:109px"><svg viewBox="0 0 16 16"><path d="M0 3h16v1.5L8 9 0 4.5z"/><path d="M0 6.3l8 4.4 8-4.4V13H0z"/></svg>info@kavmail.com</p>
    <p class="detail" style="top:147px"><svg viewBox="0 0 16 16"><path d="M3.5 1l3 3.2-1.7 2a10 10 0 0 0 5 5l2-1.7 3.2 3-2 2.5C6.5 14.5 1.5 9.5 1 3z"/></svg>+1(555) 204 7316</p>
    <p class="detail" style="top:185px"><svg viewBox="0 0 16 16"><path d="M8 0a5.5 5.5 0 0 0-5.5 5.5C2.5 10 8 16 8 16s5.5-6 5.5-10.5A5.5 5.5 0 0 0 8 0zm0 7.8a2.3 2.3 0 1 1 0-4.6 2.3 2.3 0 0 1 0 4.6z"/></svg>384 Pembrook St, Linwick KV 07912</p>
    <p class="detail" style="top:219px"><svg viewBox="0 0 16 16"><path d="M2 0h8l4 4v12H2z"/><path d="M4.5 8h7v1h-7zm0 2.5h7v1h-7z" fill="var(--dark-bg-a)"/></svg>License# 52804</p>
  </div>
  <a class="subscribe" href="#">Subscribe Now</a>
</section>

<section class="signature signature--light" aria-label="Email signature, light version">
  <svg class="pedestal" width="1026" height="342" aria-hidden="true">
    <polygon points="63,190 372,190 380,210 55,210" fill="var(--brand-red)"/>
    <rect x="33" y="217" width="148" height="10" fill="var(--bar-grey-light)"/>
    <rect x="250" y="217" width="146" height="10" fill="var(--bar-grey-light)"/>
  </svg>
  <div class="headshot" role="img" aria-label="Circular headshot of the employee"></div>

  <a class="social" href="#" aria-label="Social profile link 1" style="left:115px;top:255px"></a>
  <a class="social" href="#" aria-label="Social profile link 2" style="left:170px;top:255px"></a>
  <a class="social" href="#" aria-label="Social profile link 3" style="left:225px;top:255px"></a>
  <a class="social" href="#" aria-label="Social profile link 4" style="left:284px;top:259px"></a>

  <div class="details">
    <p class="detail" style="top:39px"><svg viewBox="0 0 16 16"><circle cx="8" cy="4.5" r="3.5"/><path d="M1 16c0-4 3-6.5 7-6.5s7 2.5 7 6.5z"/></svg>Alan Mercer</p>
    <p class="detail company" style="top:74px">KAV Fire &amp; Security</p>
    <p class="detail" style="top:109px"><svg viewBox="0 0 16 16"><path d="M0 3h16v1.5L8 9 0 4.5z"/><path d="M0 6.3l8 4.4 8-4.4V13H0z"/></svg>info@kavmail.com</p>
    <p class="detail" style="top:147px"><svg viewBox="0 0 16 16"><path d="M3.5 1l3 3.2-1.7 2a10 10 0 0 0 5 5l2-1.7 3.2 3-2 2.5C6.5 14.5 1.5 9.5 1 3z"/></svg>+1(555) 204 7316</p>
    <p class="detail" style="top:185px"><svg viewBox="0 0 16 16"><path d="M8 0a5.5 5.5 0 0 0-5.5 5.5C2.5 10 8 16 8 16s5.5-6 5.5-10.5A5.5 5.5 0 0 0 8 0zm0 7.8a2.3 2.3 0 1 1 0-4.6 2.3 2.3 0 0 1 0 4.6z"/></svg>384 Pembrook St, Linwick KV 07912</p>
    <p class="detail" style="top:219px"><svg viewBox="0 0 16 16"><path d="M2 0h8l4 4v12H2z"/><path d="M4.5 8h7v1h-7zm0 2.5h7v1h-7z" fill="var(--light-bg-b)"/></svg>License# 52804</p>
  </div>
  <a class="subscribe" href="#">Subscribe Now</a>
</section>

</body>
</html>
```